Business Card & Letterhead Design

We a financial advice company based in Australia. We provide advice to wealthy farmers.

We are changing our business name FROM Brightvale Financial TO Tallowmere Wealth and we need a new letterhead and double sided business card design

Attached is designs from our previous branding (Brightvale Financial) as it includes all the details we require on the new Tallowmere Wealth business cards and letterhead.

Need extra days to review

```html
<!DOCTYPE html>
<html lang="en">
<head>
<meta charset="utf-8">
<title>Tallowmere Wealth – Business Card Back</title>
<link rel="stylesheet" href="https://fonts.googleapis.com/css2?family=Source+Sans+3:wght@400&display=swap">
<style>
  :root {
    --paper: #ffffff;
    --slate: #5d6a71;
    --slate-text: #5f6b72;
    --on-slate: #ffffff;
    --font-body: "Source Sans 3", sans-serif;
  }
  * { margin: 0; padding: 0; box-sizing: border-box; }
  html, body {
    width: 1200px;
    height: 1000px;
    overflow: hidden;
    background: var(--paper);
    font-family: var(--font-body);
  }
  .card {
    position: relative;
    width: 1200px;
    height: 1000px;
  }
  .brand-panel {
    position: absolute;
    left: 68px;
    top: 205px;
    width: 531px;
    height: 590px;
    background: var(--slate);
    color: var(--on-slate);
  }
  .brand-name {
    position: absolute;
    left: 0;
    right: 0;
    top: 350px;
    top: 145px;
    display: flex;
    align-items: center;
    justify-content: center;
    gap: 16px;
    font-size: 34px;
    font-weight: 400;
    color: var(--on-slate);
    height: 50px;
  }
  .brand-name svg { flex: none; }
  .service-list {
    position: absolute;
    left: 0;
    right: 0;
    top: 280px;
    list-style: none;
    text-align: center;
    font-size: 38px;
    line-height: 58px;
  }
  .contact-block {
    position: absolute;
    left: 669px;
    color: var(--slate-text);
    font-size: 30px;
    line-height: 40px;
  }
  .contact-block.address { top: 307px; }
  .contact-block.licensee { top: 515px; }
</style>
</head>
<body>
  <main class="card">
    <section class="brand-panel">
      <div class="brand-name">
        <svg width="44" height="44" viewBox="0 0 44 44" aria-hidden="true">
          <circle cx="22" cy="22" r="19" fill="none" stroke="#ffffff" stroke-width="3"/>
        </svg>
        <span>Tallowmere Wealth</span>
      </div>
      <ul class="service-list">
        <li>Life &amp; TPD Insurance</li>
        <li>Income Protection</li>
        <li>Financial Planning</li>
        <li>Retirement Planning</li>
      </ul>
    </section>

    <address class="contact-block address" style="font-style: normal;">
      Suite 7C, 41 Marrow St<br>
      Riverbend QLD 4170<br>
      PO Box 5142<br>
      Eastholm QLD 4170
    </address>

    <p class="contact-block licensee">
      Keystone Advice Partners<br>
      Limited<br>
      Australian Financial Services<br>
      Licensee<br>
      Lincense Number 418302
    </p>
  </main>
</body>
</html>
```